Redesign Of loomwire Page Banner and Profile image

I just want to redesign my loomwire page to be not so busy....more clean professional dental look. I dont like stock images so much so please go down the newsfeed to use an image or two from it...so it looks personable.

https://www.loomwire.com/KLOrchidSpa/

Target Market(s)

Consumers that care about their looks

Industry/Entity Type

Dental Clinic

Requirements
Must have
• I just want to redesign my loomwire page to be not so busy....more clean professional modern look. I don't like stock images so much so please go down the newsfeed to use an image or two from it...so it looks personable.
• https://www.loomwire.com/KLOrchidSpa/
Nice to have
• I just want to redesign my loomwire page to be not so busy....more clean professional dental look. I dont like stock images so much so please go down the newsfeed to use an image or two from it...so it looks personable.
Should not have

```html
<!DOCTYPE html>
<html lang="en">
<head>
<meta charset="UTF-8">
<title>Harbor Bay Teeth Whitening Center – Laser Whitening Special</title>
<link rel="stylesheet" href="https://fonts.googleapis.com/css2?family=Libre+Baskerville:wght@700&family=Open+Sans:wght@400;600;700;800&display=swap">
<style>
  :root {
    --ink-teal: #1f5f73;
    --price-teal: #27a3c6;
    --band-teal: #72bfd1;
    --url-ink: #1c4f60;
    --text-dark: #2b2f33;
    --text-grey: #5a5f64;
    --bg-light: #f4f5f6;
    --bg-mid: #e6e8ea;
    --white: #ffffff;
  }
  * { margin: 0; padding: 0; box-sizing: border-box; }
  html, body { width: 1200px; height: 451px; overflow: hidden; background: var(--white); }
  .banner {
    position: relative;
    width: 1200px;
    height: 451px;
    overflow: hidden;
    background: radial-gradient(ellipse at 30% 45%, var(--bg-light) 0%, var(--bg-mid) 100%);
    font-family: "Open Sans", Arial, sans-serif;
  }
  .hero-photo {
    position: absolute;
    left: 620px;
    top: 0;
    width: 580px;
    height: 420px;
    background:
      radial-gradient(ellipse at 62% 48%, #e7cbb8 0%, #c99c80 30%, rgba(120,80,55,0.85) 58%, rgba(214,228,236,0.9) 85%),
      linear-gradient(90deg, #e9ecef 0%, #cfe4ee 100%);
    -webkit-mask-image: linear-gradient(90deg, transparent 0%, #000 30%);
    mask-image: linear-gradient(90deg, transparent 0%, #000 30%);
  }
  .brand {
    position: absolute;
    left: 170px;
    top: 36px;
    display: flex;
    align-items: center;
    gap: 12px;
  }
  .brand-dot {
    width: 62px;
    height: 62px;
    border-radius: 50%;
    background: var(--bg-mid);
    border: 2px solid #b9c0c6;
  }
  .brand-name {
    font-family: "Libre Baskerville", Georgia, serif;
    font-weight: 700;
    color: var(--text-grey);
    font-size: 22px;
    line-height: 1.15;
    text-transform: uppercase;
  }
  .headline {
    position: absolute;
    left: 48px;
    top: 150px;
    font-family: "Libre Baskerville", Georgia, serif;
    font-weight: 700;
    color: var(--ink-teal);
    font-size: 39px;
    line-height: 46px;
    letter-spacing: 1px;
    text-transform: uppercase;
  }
  .regular-price {
    position: absolute;
    left: 254px;
    top: 244px;
    font-weight: 700;
    font-size: 17px;
    color: var(--text-dark);
    letter-spacing: 0.5px;
  }
  .schedule {
    position: absolute;
    left: 87px;
    top: 326px;
    font-weight: 800;
    font-size: 18px;
    color: var(--text-dark);
    text-transform: uppercase;
    word-spacing: 2px;
  }
  .special {
    position: absolute;
    left: 620px;
    top: 234px;
    width: 200px;
    text-align: center;
  }
  .special-label {
    font-weight: 700;
    font-size: 20px;
    line-height: 24px;
    color: var(--text-grey);
    text-transform: uppercase;
  }
  .special-price {
    font-weight: 800;
    font-size: 60px;
    line-height: 70px;
    color: var(--price-teal);
    text-shadow: 1px 2px 3px rgba(0,0,0,0.3);
  }
  .footer-band {
    position: absolute;
    left: 0;
    bottom: 0;
    width: 1200px;
    height: 80px;
  }
  .website {
    position: absolute;
    left: 0;
    bottom: 14px;
    width: 1200px;
    text-align: center;
    font-weight: 600;
    font-size: 25px;
    color: var(--url-ink);
  }
</style>
</head>
<body>
  <div class="banner">
    <div class="hero-photo" role="img" aria-label="Photo of a smiling woman with long dark hair and white teeth against a bright sky"></div>

    <div class="brand">
      <span class="brand-dot"></span>
      <div class="brand-name">Harbor Bay<br>Teeth Whitening Center</div>
    </div>

    <h1 class="headline">Professional Laser<br>Teeth Whitening</h1>
    <p class="regular-price">REG $378</p>

    <p class="schedule">Schedule an app today&nbsp; 888. 555. 019</p>

    <div class="special">
      <p class="special-label">Limited Time<br>Special</p>
      <p class="special-price">$99</p>
    </div>

    <svg class="footer-band" viewBox="0 0 1200 80" preserveAspectRatio="none" aria-hidden="true">
      <path d="M0 38 Q560 -14 1200 26 L1200 80 L0 80 Z" fill="var(--white)"/>
      <path d="M0 46 Q560 -4 1200 34 L1200 80 L0 80 Z" fill="var(--band-teal)"/>
    </svg>
    <p class="website">www.HarborBayTeethWhitening.com</p>
  </div>
</body>
</html>
```